Sell the dream! Property investment proposal document

We are looking for a proposal document which outlines our vision for property development. The purpose of the document is to raise investment from investors - sell the dream!
Brief summary:
Kestrel Dwellings Developments, is an emerging New Zealand property investment company with a focus on providing unique property investment opportunities.
Our expertise and capabilities in architectural modular homes provide us with a remarkable advantage in tackling the development of properties that are typically considered challenging, remote, or uniquely positioned.
Our specialization in this niche sector of property development not only sets us apart from competitors, but also paves the way for lucrative investment opportunities in the New Zealand property market.
Feel free to use any images from www.kestreldwellings.co.nz
Target Market(s)
investors for a unique property development opportunity
Industry/Entity Type
luxury property development in unique locations throughout New Zealand
Colors
Designer to choose only greyscale colors for use in the design.
Look and feel

```html
<!DOCTYPE html>
<html lang="en">
<head>
<meta charset="utf-8">
<title>Kestrel Dwellings – Investment Proposal</title>
<link rel="stylesheet" href="https://fonts.googleapis.com/css2?family=Roboto:wght@300;400;500;700&display=swap">
<style>
  :root {
    --backdrop: #dcdedd;
    --paper: #f4f4f4;
    --charcoal: #333331;
    --ink: #2b2b2a;
    --text-light: #f2f2f0;
    --sky-top: #dfe6ee;
    --sky-mid: #eef1f3;
  }
  * { margin: 0; padding: 0; box-sizing: border-box; }
  html, body { width: 1200px; height: 2162px; overflow: hidden; }
  body {
    background: var(--backdrop);
    font-family: "Roboto", Arial, sans-serif;
    position: relative;
  }
  .page {
    position: absolute;
    width: 389px;
    height: 549px;
    overflow: hidden;
    box-shadow: 8px 10px 14px rgba(0,0,0,0.14);
  }
  .page--light { background: var(--paper); color: var(--ink); }
  .page--dark { background: var(--charcoal); color: var(--text-light); }

  .photo { position: absolute; }
  .section-title {
    position: absolute;
    font-size: 11.5px;
    font-weight: 700;
    letter-spacing: 0.1px;
  }
  .body-copy {
    position: absolute;
    font-size: 7.3px;
    line-height: 9.3px;
    font-weight: 400;
  }
  .body-copy p + p { margin-top: 9.3px; }
  .body-copy strong { font-weight: 700; }

  .brand-row {
    position: absolute;
    left: 37px; right: 37px;
    display: flex;
    justify-content: space-between;
    align-items: center;
  }
  .brand-name { font-size: 26px; font-weight: 400; color: var(--ink); letter-spacing: -0.5px; }
  .brand-tag { display: flex; align-items: center; gap: 6px; font-size: 8px; font-weight: 400; color: var(--ink); }
  .brand-tag .mark { width: 7px; height: 7px; background: var(--ink); }

  /* page 1 – cover */
  .cover { left: 128px; top: 128px; }
  .cover .photo { left: 37px; top: 37px; width: 315px; height: 415px;
    background: linear-gradient(180deg, #cfcbc0 0%, #e6dccb 35%, #8c7f6d 55%, #3b3530 75%, #2a2724 100%); }
  .cover-headline {
    position: absolute; left: 74px; top: 343px;
    font-size: 22px; line-height: 23.5px; font-weight: 700; color: #fff;
  }
  .cover .brand-row { top: 490px; }

  /* page 2 – overview */
  .overview { left: 683px; top: 128px; }
  .overview .photo { left: 194px; top: 37px; width: 195px; height: 475px;
    background: linear-gradient(180deg, #e4e7ea 0%, #dcdfe2 55%, #3a3b38 60%, #2c2d2a 80%, #6d6a4c 100%); }
  .overview .section-title { left: 36px; top: 100px; }
  .overview .body-copy { left: 36px; top: 127px; width: 130px; }

  /* page 3 – origins */
  .origins { left: 159px; top: 806px; }
  .origins .photo--side { left: 0; top: 37px; width: 97px; height: 474px;
    background: linear-gradient(180deg, #e3e6e8 0%, #d7dadc 55%, #4a4a45 62%, #5f6150 80%, #8c8660 100%); }
  .origins .photo--bedroom { left: 134px; top: 37px; width: 255px; height: 159px;
    background: linear-gradient(90deg, #5a5550 0%, #9c968d 40%, #c6c9cb 70%, #d8d6d0 100%); }
  .origins .section-title { left: 134px; top: 231px; }
  .origins .body-copy { left: 134px; top: 258px; width: 222px; }

  /* page 4 – advantage */
  .advantage { left: 683px; top: 806px; color: var(--ink);
    background: linear-gradient(180deg, var(--sky-top) 0%, var(--sky-mid) 40%, #e9ecee 60%, #3a3a38 62%, #5f7a3c 80%, #7fa63a 100%); }
  .advantage .section-title { left: 36px; top: 36px; color: var(--ink); }
  .advantage .body-copy { left: 36px; top: 63px; width: 318px; color: #3a3a3a; }

  /* page 5 – financials */
  .financials { left: 165px; top: 1484px; }
  .financials .section-title { left: 37px; top: 36px; }
  .financials .body-copy { left: 37px; top: 63px; width: 322px; }
  .financials .photo { left: 0; top: 257px; width: 389px; height: 254px;
    background: linear-gradient(180deg, #8f8878 0%, #a9a08a 25%, #5e5a3e 45%, #4b4a2c 70%, #3b3a24 100%); }

  /* page 6 – back cover */
  .back { left: 683px; top: 1484px; }
  .back-panel { position: absolute; left: 37px; top: 37px; width: 314px; height: 415px; background: var(--charcoal); }
  .contact {
    position: absolute; left: 0; right: 0; top: 347px;
    text-align: center; color: var(--text-light);
    font-size: 7.3px; line-height: 9.3px;
  }
  .contact .name { font-weight: 700; }
  .contact .gap { height: 9.3px; }
  .back .brand-row { top: 490px; }
</style>
</head>
<body>

  <section class="page page--light cover">
    <div class="photo" role="img" aria-label="Modular glass pavilion cantilevered over a hillside at dusk"></div>
    <h1 class="cover-headline">Delivered and<br>connected<br>anywhere</h1>
    <div class="brand-row">
      <span class="brand-name">Kestrel</span>
      <span class="brand-tag"><span class="mark"></span>Kestrel Dwellings</span>
    </div>
  </section>

  <section class="page page--dark overview">
    <h2 class="section-title">Business Overview</h2>
    <div class="body-copy">
      <p>Kestrel Dwellings Developments, is an emerging New Zealand property investment company with a focus on providing unique property investment opportunities.</p>
      <p>Our expertise and capabilities in architectural modular homes provide us with a remarkable advantage in tackling the development of properties that are typically considered challenging, remote, or uniquely positioned.</p>
      <p>As a company, with 48 employees boasting a wealth of experience in handling complex architectural projects, making us well-equipped to navigate the intricacies and demands of such ventures.</p>
      <p>This advantage allows us to not only execute projects efficiently but also to deliver exceptional results within condensed time frames.</p>
      <p>By capitalizing on our ability to develop difficult, remote, or one-of-a-kind properties swiftly and effectively, <strong>Kestrel Dwellings Developments</strong> offers investors a rare chance to engage in projects that promise exceptional profitability in the New Zealand property market.</p>
      <p>Our specialization in this niche sector of property development not only sets us apart from competitors, but also paves the way for lucrative investment opportunities in the New Zealand property market.</p>
    </div>
    <div class="photo" role="img" aria-label="Dark modular home with glass frontage behind tall grasses"></div>
  </section>

  <section class="page page--dark origins">
    <div class="photo photo--side" role="img" aria-label="Covered veranda of a modular home among trees and grasses"></div>
    <div class="photo photo--bedroom" role="img" aria-label="Bedroom interior with a large window overlooking the sea"></div>
    <h2 class="section-title">Business Origins</h2>
    <div class="body-copy">
      <p>Kestrel Dwellings Developments was established with the goal of transforming the property investment market in New Zealand by introducing an innovative approach that centers on architectural modular designs and streamlined project timelines.</p>
      <p>Driven by our enthusiasm for architecture and real estate, we have expanded our successful business model to not only offer financial opportunities for investors but also to expand on our passion for high-end architectural design.</p>
      <p>With a wealth of experience accumulated over the past six years in the construction and the property market, we are pivoting to focus solely on our property development initiatives, presenting completed Kestrel projects to the market, in exclusive locations.</p>
      <p>These projects will boast high-quality standards, meticulous attention to detail and landscaping, and creative design elements.</p>
      <p>By introducing completed Kestrel properties into the market, we aim to reach a wider audience, catering to individuals who prefer ready-to-occupy homes, over engaging in the design and construction process. This approach also simplifies the financing process for prospective buyers, as established properties are often preferred by financial lenders.</p>
    </div>
  </section>

  <section class="page advantage" role="img" aria-label="Slatted modular home cantilevered over a grassy rocky slope by the sea">
    <h2 class="section-title">Competitive Advantage</h2>
    <div class="body-copy">
      <p>Our competitive advantage lies in the uniqueness of our property investment opportunities. Unlike traditional real estate companies, we focus on offering properties that are not only profitable but also aesthetically pleasing and unique. By catering to the tastes of architecture lovers, we set ourselves apart from the competition and attract a niche market of customers who appreciate the artistry and design of our projects.</p>
      <p>Additionally, the streamlined and condensed timelines facilitated by our modular approach provide quicker returns on investment.</p>
    </div>
  </section>

  <section class="page page--dark financials">
    <h2 class="section-title">Financial Summary</h2>
    <div class="body-copy">
      <p>In terms of financial projections, with each development, we anticipate a profit of 10%-20% which will be project dependent.</p>
      <p>This growth is fueled by the increasing demand for unique property investments in New Zealand and our ability to deliver high-quality services to the market in a condensed time frame, with heavily controlled costs.</p>
      <p>With a solid business model and a dedicated team, we are confident in our ability to achieve success and establish Kestrel Dwellings Investments as a trusted name in the industry.</p>
      <p>New Zealand's property market has been experiencing steady growth over the years, making it an attractive destination for property investors. With its beautiful landscapes and strong economy, New Zealand offers a diverse range of investment opportunities for both local and international investors. The demand for quality properties in prime locations continues to rise, creating a favorable environment for property investment companies like ours that can lean on our modular benefits of being able to reach unique and remote locations.</p>
    </div>
    <div class="photo" role="img" aria-label="Low modular home on coastal farmland at golden hour"></div>
  </section>

  <section class="page page--light back">
    <div class="back-panel">
      <div class="contact">
        <div class="name">Mara Ellison</div>
        <div>Sales Manager</div>
        <div class="gap"></div>
        <div>+64 21 555 0147</div>
        <div>mara@kestreldwellings.co.nz</div>
        <div>Kestreldwellings.co.nz</div>
        <div>@kestreldwellings</div>
      </div>
    </div>
    <div class="brand-row">
      <span class="brand-name">Kestrel</span>
      <span class="brand-tag"><span class="mark"></span>Kestrel Dwellings</span>
    </div>
  </section>

</body>
</html>
```